Salmon Shop that sells both wholesale and retail salmon in a variety of ways.

"Reef Harvest" is a business that is selling atlantic salmon in every way possible. We will be a salmon butcher to the public for retail purchase and we will also be out and about trying to sell our products to restaurants cafes and any other wholesale way. Our product is from Tasmania but we will be trading on the Sunshine Coast. The shop design has an urban, rustic feel and very much about the product. One of the owners has worked on salmon farms for 15 years and we want it to be very specialised and quality. I have nothing to offer you to help with this design....I would like both a salmon on the card, not sure if image or silohette is best and would like the other side to have a fillet with a tag of some sort. We are looking for a logo also. Use a photo of an Atlantic Salmon, Atlantic Salmon have two fins along the back.
Updates

Project Deadline Extended Reason: I am extending the deadline as I have still not got exactly what I want. All designers have added something great to what I am after and I just need someone to pull it all together. I have put in a new brief with a sketched image to help so we can get this perfect. Please read all the instructions. Thank you Added Monday, February 16, 2015

Target Market(s)

Restaurants, cafes

Industry/Entity Type

Retail

Contact Information for Business Card

Reef Harvest (Not to have "Shop" at the end.Shop 12/130-164 Brisbane RdMooloolaba 4557

Colors
1c66ab

Requirements
Must have
• logo for reef harvest with the S being salmon fillet of fresh salmon on white platemap of tasmaniasepia /black and white image of atlantic salmon
Nice to have
• fillet of salmonmap of tasmaniasalmon
Should not have
• Not Shop at the end.

```html
<!DOCTYPE html>
<html lang="en">
<head>
<meta charset="utf-8">
<title>Reef Harvest – Business Card</title>
<link href="https://fonts.googleapis.com/css2?family=Righteous&display=swap" rel="stylesheet">
<style>
  :root {
    --page: #ffffff;
    --wood-light: #ddccb0;
    --wood-mid: #cdb894;
    --wood-dark: #bfa67f;
    --ink: #3a3836;
    --salmon: #f05a28;
  }
  html, body {
    margin: 0;
    padding: 0;
    width: 955px;
    height: 1200px;
    overflow: hidden;
    background: var(--page);
    font-family: "Righteous", sans-serif;
    color: var(--ink);
  }
  .canvas {
    position: relative;
    width: 955px;
    height: 1200px;
  }
  .card {
    position: absolute;
    left: 51px;
    width: 853px;
    overflow: hidden;
  }
  .card--front { top: 46px; height: 527px; }
  .card--back { top: 619px; height: 528px; }
  .card__wood {
    position: absolute;
    inset: 0;
    background: linear-gradient(100deg, var(--wood-mid) 0%, var(--wood-light) 35%, var(--wood-mid) 65%, var(--wood-dark) 100%);
  }
  .brand {
    position: absolute;
    display: flex;
    align-items: center;
  }
  .brand__name {
    margin: 0;
    text-align: right;
    font-weight: 400;
    line-height: 0.95;
    color: var(--ink);
  }
  .brand__dot {
    border-radius: 50%;
    background: var(--salmon);
    flex: none;
  }
  .card--front .brand { left: 160px; top: 169px; height: 250px; gap: 40px; }
  .card--front .brand__name { font-size: 104px; }
  .card--front .brand__dot { width: 150px; height: 150px; }

  .card--back .brand { left: 110px; top: 151px; height: 150px; gap: 22px; }
  .card--back .brand__name { font-size: 58px; }
  .card--back .brand__dot { width: 84px; height: 84px; }

  .contact {
    position: absolute;
    left: 575px;
    top: 214px;
    width: 160px;
    text-align: center;
    font-size: 38px;
    line-height: 1.1;
  }
  .contact p { margin: 0; }
  .address {
    position: absolute;
    left: 50px;
    top: 345px;
    font-size: 28px;
    line-height: 1.25;
    transform: rotate(-8deg);
    transform-origin: left top;
    text-align: right;
  }
  .address p { margin: 0; }
</style>
</head>
<body>
<main class="canvas">
  <section class="card card--front">
    <div class="card__wood" role="img" aria-label="Light natural wood grain texture"></div>
    <div class="brand">
      <h1 class="brand__name">Reef<br>Harvest</h1>
      <span class="brand__dot"></span>
    </div>
  </section>

  <section class="card card--back">
    <div class="card__wood" role="img" aria-label="Light natural wood grain texture"></div>
    <div class="brand">
      <h2 class="brand__name">Reef<br>Harvest</h2>
      <span class="brand__dot"></span>
    </div>
    <div class="contact">
      <p class="contact__name">NED</p>
      <p class="contact__phone">875512340</p>
    </div>
    <address class="address" style="font-style:normal">
      <p>Shop 7/212-238 Kellaway Rd</p>
      <p>Coolum 4573</p>
    </address>
  </section>
</main>
</body>
</html>
```